Business Cards for Volmont Hayes, a law firm

We changed our firm's name from "Volmont & Hayes LLP" to "Volmont Hayes", we need to update our cards with a new design. We like the overall look of the back but the front side of the cards (see attached mockup) needs a refreshed look. I also attach our current logo so you can get rid of that LLP and &. We have a new address as well (not same as on mockup).

Target Market(s)

Clients of law firm

Industry/Entity Type

Law Firm

Contact Information for Business Card

Frontsides:

Lorenzo T. Volmont
Partner
Tel: (416) 555-0172 ext. 101
Fax: (647) 555-0139
Email: lvolmont@vhlegal.example

Simon P. Hayes
Partner
Tel: (416) 555-0172 ext. 102
Fax: (647) 555-0139
Email: simonhayes@vhlegal.example

Mark E. Dorsan
Barrister
Tel: (416) 555-0172 ext. 104
Fax: (647) 555-0139
Email: mdorsan@vhlegal.example

The back side should be crimson red (see mockup) with the logo (please update it to remove the & and the LLP, you can modify it a bit to make it tasteful if need be). Our new address is

82 Marlow Rd W, Suite 710
Toronto, ON M5K 0Z9

After our address, please also include our website www.vhlegal.example

Font styles to use
Sans Serif

Colors
ec2027
ffffff
000000

Requirements
Must have
• PLEASE NOTE: our firm's colour is more of a darker/crimson red, not a vibrant red.
• The front should have space for the lawyer's name, title, phone number (with extension), fax number, and email.
• If you're going to add those yourself, the info for the frontside is in the "Business Card Details" section (three lawyers that need their own cards).
Nice to have
• We like the backside of our current cards, just update it with our new address (one address now instead of 2), and a slightly modified logo (not a new logo altogether).
• The frontside should be refreshed with a better look (think minimalist, professional and modern), although still predominantly white-based background.
Should not have
• No scales of justice or other cheesy lawyer stereotype symbols! :-)

```html
<!DOCTYPE html>
<html lang="en">
<head>
<meta charset="utf-8">
<title>Volmont Hayes — Business Cards</title>
<link rel="stylesheet" href="https://fonts.googleapis.com/css2?family=Rubik:wght@400;500;700&display=swap">
<style>
  :root {
    --crimson: #c01f17;
    --crimson-line: #6e0f0b;
    --white: #ffffff;
    --black: #111111;
    --page: #f3f3f3;
    --rule: #e6e6e6;
  }
  * { box-sizing: border-box; margin: 0; padding: 0; }
  html, body {
    width: 1200px; height: 954px; overflow: hidden;
    background: var(--page);
    font-family: "Rubik", Arial, sans-serif;
  }
  .sheet { position: relative; width: 1200px; height: 954px; }

  .card-back {
    position: absolute; left: 23px; width: 564px; height: 284px;
    background: var(--crimson);
    color: var(--white);
  }
  .card-back .firm-name {
    position: absolute; left: 0; right: 0; top: 80px;
    text-align: center;
    font-size: 38px; font-weight: 700; letter-spacing: 0.2px;
  }
  .card-back .divider {
    position: absolute; left: 0; right: 0; top: 204px;
    height: 1.5px; background: var(--crimson-line);
  }
  .card-back .address {
    position: absolute; left: 28px; top: 228px;
    font-size: 11.5px; font-weight: 500; line-height: 16px;
  }
  .card-back .website {
    position: absolute; right: 34px; top: 236px;
    font-size: 12.5px; font-weight: 500; letter-spacing: 0.3px;
  }

  .card-front {
    position: absolute; left: 618px; width: 553px; height: 282px;
    background: var(--white);
    box-shadow: 0 3px 8px rgba(0,0,0,0.12);
  }
  .card-front .firm-name {
    position: absolute; left: 0; width: 250px; top: 128px;
    text-align: center;
    font-size: 20px; font-weight: 700; color: var(--crimson);
  }
  .card-front .divider {
    position: absolute; left: 249px; top: 45px;
    width: 3px; height: 192px; background: var(--rule);
  }
  .card-front .details { position: absolute; left: 314px; top: 88px; }
  .card-front .person-name {
    font-size: 15px; font-weight: 700; color: var(--black); letter-spacing: 0.4px;
  }
  .card-front .person-title {
    font-size: 13px; color: var(--crimson); margin-top: 1px;
  }
  .card-front .contact-list { list-style: none; margin-top: 24px; }
  .card-front .contact-list li {
    display: flex; align-items: center; gap: 8px;
    font-size: 13px; line-height: 17px; color: var(--black); letter-spacing: 0.3px;
  }
  .card-front .contact-list svg { width: 10px; height: 10px; fill: var(--crimson); flex: none; }
</style>
</head>
<body>
<main class="sheet">
  <svg width="0" height="0" style="position:absolute">
    <defs>
      <symbol id="icon-phone" viewBox="0 0 10 10"><path d="M2 0.5 L3.6 0.5 L4.2 2.8 L3.1 3.6 Q4 5.8 6.2 6.9 L7 5.8 L9.5 6.4 L9.5 8 Q9.5 9.5 8 9.5 Q0.5 9 0.5 2 Q0.5 0.5 2 0.5Z"/></symbol>
      <symbol id="icon-fax" viewBox="0 0 10 10"><rect x="2.5" y="0.5" width="5" height="3"/><rect x="0.5" y="3.5" width="9" height="4.5" rx="1"/><rect x="2.5" y="7" width="5" height="2.5" fill="#fff"/><rect x="3" y="7.5" width="4" height="2"/></symbol>
      <symbol id="icon-mail" viewBox="0 0 10 10"><path d="M0.5 2 L9.5 2 L9.5 8.5 L0.5 8.5Z M1.2 2.6 L5 5.6 L8.8 2.6" /></symbol>
    </defs>
  </svg>

  <section class="card-back" style="top:21px">
    <div class="firm-name">Volmont Hayes</div>
    <div class="divider"></div>
    <p class="address">82 Marlow Rd W, Suite 710<br>Toronto, ON M5K 0Z9</p>
    <p class="website">www.vhlegal.example</p>
  </section>
  <section class="card-front" style="top:21px">
    <div class="firm-name">Volmont Hayes</div>
    <div class="divider"></div>
    <div class="details">
      <p class="person-name">Lorenzo T. Volmont</p>
      <p class="person-title">Partner</p>
      <ul class="contact-list">
        <li><svg><use href="#icon-phone"/></svg>(416) 555-0172 ext. 101</li>
        <li><svg><use href="#icon-fax"/></svg>(647) 555-0139</li>
        <li><svg><use href="#icon-mail"/></svg>lvolmont@vhlegal.example</li>
      </ul>
    </div>
  </section>

  <section class="card-back" style="top:328px">
    <div class="firm-name">Volmont Hayes</div>
    <div class="divider"></div>
    <p class="address">82 Marlow Rd W, Suite 710<br>Toronto, ON M5K 0Z9</p>
    <p class="website">www.vhlegal.example</p>
  </section>
  <section class="card-front" style="top:327px">
    <div class="firm-name">Volmont Hayes</div>
    <div class="divider"></div>
    <div class="details">
      <p class="person-name">Simon P. Hayes</p>
      <p class="person-title">Partner</p>
      <ul class="contact-list">
        <li><svg><use href="#icon-phone"/></svg>(416) 555-0172 ext. 102</li>
        <li><svg><use href="#icon-fax"/></svg>(647) 555-0139</li>
        <li><svg><use href="#icon-mail"/></svg>simonhayes@vhlegal.example</li>
      </ul>
    </div>
  </section>

  <section class="card-back" style="top:636px">
    <div class="firm-name">Volmont Hayes</div>
    <div class="divider"></div>
    <p class="address">82 Marlow Rd W, Suite 710<br>Toronto, ON M5K 0Z9</p>
    <p class="website">www.vhlegal.example</p>
  </section>
  <section class="card-front" style="top:634px">
    <div class="firm-name">Volmont Hayes</div>
    <div class="divider"></div>
    <div class="details">
      <p class="person-name">Mark E. Dorsan</p>
      <p class="person-title">Barrister</p>
      <ul class="contact-list">
        <li><svg><use href="#icon-phone"/></svg>(416) 555-0172 ext. 104</li>
        <li><svg><use href="#icon-fax"/></svg>(647) 555-0139</li>
        <li><svg><use href="#icon-mail"/></svg>mdorsan@vhlegal.example</li>
      </ul>
    </div>
  </section>
</main>
</body>
</html>
```